American cannabis tech company business card design

Pavrel.com is seeking a modern, professional, and brand-aligned business card that represents our company and its core values: Mission, Story, Values, and Impact. As an innovative cannabis company, we want a business card that is not only visually appealing but also serves as a representation of who we are and what we stand for.

Project Scope: Design a double-sided business card that integrates our brand identity and core values. Incorporate our key brand elements, ensuring a sleek and contemporary aesthetic. Visually reflect our core values (Mission, Story, Values, Impact) in a way that is engaging yet professional.

Target Market(s)

Vendors, third parties,

Contact Information for Business Card

Contact details (name, title, email, phone, website, etc.)

Font styles to use
Other font styles liked:
• Caslon, Centra

Colors

Designer to choose colors to be used in the design.

Requirements
Must have
• Pavrel.com logo and branding A creative yet clean way to integrate our core values (Mission, Story, Values, Impact) Modern typography and a well-structured layout
Nice to have
• forest green, grey, white, black
Should not have
• references to marijuana, leafs, plants, or related product

```html
<!DOCTYPE html>
<html lang="en">
<head>
<meta charset="UTF-8">
<title>Pavrel Business Card</title>
<link href="https://fonts.googleapis.com/css2?family=Poppins:wght@400;500;600;800&display=swap" rel="stylesheet">
<style>
  :root {
    --forest: #1a3319;
    --paper: #efefef;
    --paper-soft: #e4e4e4;
    --swoosh-grey: #a9a9a9;
    --ink-light: #f2f2f2;
    --backdrop: #2b2b2b;
  }
  * { margin: 0; padding: 0; box-sizing: border-box; }
  html, body {
    width: 1200px; height: 1200px; overflow: hidden;
    background: var(--backdrop);
    font-family: "Poppins", sans-serif;
  }
  .stage { position: relative; width: 1200px; height: 1200px; }
  .card {
    position: absolute; left: 200px; width: 798px; height: 454px;
    border-radius: 20px; overflow: hidden;
  }
  .card-front { top: 96px; background: linear-gradient(160deg, #f6f6f6, var(--paper-soft)); }
  .card-back { top: 656px; background: var(--forest); color: var(--ink-light); }

  .front-waves { position: absolute; inset: 0; width: 100%; height: 100%; }
  .brand-name {
    position: absolute; left: 72px; top: 128px;
    font-weight: 800; font-size: 60px; letter-spacing: 1px;
    color: var(--forest); line-height: 1;
  }
  .person { position: absolute; right: 42px; top: 238px; text-align: right; }
  .person-name { font-weight: 600; font-size: 32px; color: var(--ink-light); line-height: 1.1; letter-spacing: 0.5px; }
  .person-title { font-weight: 400; font-size: 22px; color: var(--ink-light); margin-top: 4px; letter-spacing: 0.5px; }
  .contact-list { position: absolute; right: 44px; top: 330px; list-style: none; }
  .contact-item {
    display: flex; align-items: center; justify-content: flex-end; gap: 14px;
    font-size: 19px; color: var(--ink-light); letter-spacing: 1px; height: 32px;
  }
  .contact-icon { width: 17px; height: 17px; flex: none; }

  .value-block { position: absolute; width: 330px; }
  .value-heading {
    display: inline-block; font-weight: 800; font-size: 18px; letter-spacing: 0.3px;
    border-bottom: 2px solid var(--ink-light); line-height: 1.25; padding-bottom: 1px;
  }
  .value-text { font-size: 15px; line-height: 18.6px; margin-top: 8px; font-weight: 400; }
  .block-mission { left: 46px; top: 56px; }
  .block-story { left: 46px; top: 203px; }
  .block-values { left: 402px; top: 56px; width: 340px; }
  .block-impact { left: 402px; top: 240px; width: 364px; }
</style>
</head>
<body>
<main class="stage">
  <section class="card card-front" aria-label="Business card front">
    <svg class="front-waves" viewBox="0 0 997 568" preserveAspectRatio="none" aria-hidden="true">
      <path fill="var(--forest)" d="M0,568 V355 C120,395 300,420 470,300 C620,190 780,118 900,126 C950,130 980,150 997,172 V568 Z"/>
      <path fill="var(--paper)" d="M0,392 C170,440 360,430 530,255 C380,400 210,470 0,465 Z"/>
      <path fill="var(--swoosh-grey)" d="M240,447 C430,425 560,270 700,175 C780,125 860,115 915,128 C850,126 770,150 690,208 C560,305 430,430 240,447 Z"/>
    </svg>
    <div class="brand-name">PAVREL</div>
    <div class="person">
      <div class="person-name">OWEN MARSH</div>
      <div class="person-title">Co-founder &amp; CEO</div>
    </div>
    <ul class="contact-list">
      <li class="contact-item">+1 555-014-2290
        <svg class="contact-icon" viewBox="0 0 24 24" aria-hidden="true"><path fill="none" stroke="var(--ink-light)" stroke-width="2.2" stroke-linecap="round" stroke-linejoin="round" d="M5 3h4l2 5-2.5 1.5a11 11 0 0 0 6 6L16 13l5 2v4a2 2 0 0 1-2 2A17 17 0 0 1 3 5a2 2 0 0 1 2-2zM15 3a6 6 0 0 1 6 6M15 7a2 2 0 0 1 2 2"/></svg>
      </li>
      <li class="contact-item">team@pavrel.com
        <svg class="contact-icon" viewBox="0 0 24 24" aria-hidden="true"><rect x="2" y="5" width="20" height="14" rx="1.5" fill="var(--ink-light)"/><path d="M3 6l9 7 9-7" fill="none" stroke="var(--forest)" stroke-width="1.8"/></svg>
      </li>
      <li class="contact-item">pavrel.com
        <svg class="contact-icon" viewBox="0 0 24 24" aria-hidden="true"><circle cx="12" cy="12" r="10" fill="var(--ink-light)"/><path d="M7 7c2 1 3 3 2 5s1 3 2 5M15 4c-1 2 0 4 2 4s3 2 2 4" fill="none" stroke="var(--forest)" stroke-width="2"/></svg>
      </li>
    </ul>
  </section>

  <section class="card card-back" aria-label="Business card back">
    <article class="value-block block-mission">
      <h2 class="value-heading">MISSION</h2>
      <p class="value-text">We think cannabis should be accessible, affordable, convenient, and transparent. But most importantly, we believe in supporting the American farmers who make all of this possible.</p>
    </article>
    <article class="value-block block-story">
      <h2 class="value-heading">STORY</h2>
      <p class="value-text">Founded in 2022 by Owen Marsh and Lena Hollis, Pavrel now has a global team of 200+ full-time employees in addition to our robust network of small, U.S. farmers and manufacturing partners. We've built partnerships with over 50 small American farms, bolstering local economies and promoting sustainable farming practices.</p>
    </article>
    <article class="value-block block-values">
      <h2 class="value-heading">VALUES</h2>
      <p class="value-text">At our core is a commitment to product quality and world-class customer experiences. Our company culture fosters open communication &amp; open doors: everybody here has a voice, &amp; we believe that by investing in both our people &amp; our customers, we all will rise.</p>
    </article>
    <article class="value-block block-impact">
      <h2 class="value-heading">IMPACT</h2>
      <p class="value-text">Social impact is a business pillar, not an afterthought. This year, we've donated tens of thousands of dollars to pet humane societies. We've contributed to the campaigns of politicians who advocate for cannabis, contributing to the broader movement toward recognition &amp; acceptance.</p>
    </article>
  </section>
</main>
</body>
</html>
```